Hvac and insulation company needs good looking business card design

We are hvac and insulation company and looking for a new business cards that look to today standards designs

Target Market(s)

homeowners

Industry/Entity Type

Hvac

Contact Information for Business Card

Name: Walter Brinoku
Home comfort consultant
address: 4827 Dunmore St #215 Oakland, CA 94619
office: 888-316-2790
cell: 510-742-3185
Lic.# 584261
Email: walter@corvane-hvac.com
Web: corvane-hvac.com

Requirements
Must have
• clean and sleek look
Nice to have
• simple with a clean look
Should not have
• to busy business card

```html
<!DOCTYPE html>
<html lang="en">
<head>
<meta charset="utf-8">
<title>Corvane Business Card</title>
<link rel="stylesheet" href="https://fonts.googleapis.com/css2?family=Roboto:wght@300;400;500&display=swap">
<style>
  :root{
    --bg:#2a2a2a;
    --orange:#f7931e;
    --orange-faint:#3a2a1a;
    --white:#ffffff;
    --paper:#f6f6f6;
    --ink:#3c3c3c;
    --muted:#8a8a8a;
    --black:#151515;
  }
  *{margin:0;padding:0;box-sizing:border-box}
  html,body{width:1200px;height:886px;overflow:hidden;background:var(--bg);font-family:"Roboto",sans-serif}
  .stage{width:1200px;height:886px;display:flex;flex-direction:column;align-items:center;justify-content:center;gap:44px}
  .card{width:560px;height:320px;border-radius:18px;position:relative;overflow:hidden}

  /* back */
  .card-back{background:var(--black)}
  .back-mark{position:absolute;left:250px;top:40px;width:260px;height:260px;border-radius:24px;background:var(--orange-faint);opacity:.8}
  .back-brand{position:absolute;left:-80px;top:110px;width:280px;height:100px;transform:rotate(-90deg);
    display:flex;flex-direction:column;justify-content:center;align-items:center;color:var(--white);text-align:center}
  .back-name{font-size:50px;font-weight:500;line-height:1;letter-spacing:-1px}
  .back-tag{font-size:14px;font-weight:300;letter-spacing:2px;margin-top:4px}
  .back-web{font-size:12px;font-weight:300;letter-spacing:4px;margin-top:3px}

  /* front */
  .card-front{background:var(--paper)}
  .brand{position:absolute;left:52px;top:96px;display:flex;align-items:center;gap:14px}
  .brand-square{width:30px;height:30px;background:var(--orange);border-radius:4px}
  .brand-name{font-size:48px;font-weight:500;color:var(--orange);line-height:1;letter-spacing:-0.5px}
  .brand-tag{position:absolute;left:98px;top:148px;font-size:14px;font-weight:300;letter-spacing:2.5px;color:var(--muted)}
  .divider{position:absolute;left:292px;top:30px;width:1px;height:190px;
    background:linear-gradient(to bottom,transparent,#b8b8b8 40%,#b8b8b8 60%,transparent)}
  .contact{position:absolute;left:312px;top:36px;color:var(--ink)}
  .contact-name{font-size:19px;font-weight:500;color:var(--orange);text-transform:uppercase;letter-spacing:-0.3px}
  .contact-title{font-size:12.5px;color:var(--muted);text-transform:uppercase;margin-bottom:12px}
  .contact-address{font-size:12.5px;line-height:1.35;margin-bottom:10px}
  .contact-list{list-style:none;font-size:12.5px;line-height:1.55}
  .contact-list li{display:flex;align-items:center;gap:8px}
  .contact-list svg{width:11px;height:11px;fill:var(--orange);flex:none}
  .web-band{position:absolute;left:30px;right:36px;bottom:28px;height:30px;background:var(--orange);border-radius:15px 0 0 15px;
    display:flex;align-items:center;justify-content:center;color:var(--white);font-size:13px;letter-spacing:6px}
  .band-end{position:absolute;right:20px;bottom:28px;width:30px;height:30px;background:var(--orange);
    clip-path:polygon(0 0,60% 0,100% 50%,60% 100%,0 100%)}
</style>
</head>
<body>
<main class="stage">
  <section class="card card-back" aria-label="Card back">
    <div class="back-mark" role="img" aria-label="Faint brand square decoration"></div>
    <div class="back-brand">
      <span class="back-name">corvane</span>
      <span class="back-tag">home solutions</span>
      <span class="back-web">corvane-hvac.com</span>
    </div>
  </section>

  <section class="card card-front" aria-label="Card front">
    <div class="brand">
      <span class="brand-square"></span>
      <span class="brand-name">corvane</span>
    </div>
    <div class="brand-tag">home solutions</div>
    <div class="divider"></div>
    <div class="contact">
      <p class="contact-name">Walter Brinoku</p>
      <p class="contact-title">Home Comfort Consultant</p>
      <p class="contact-address">4827 Dunmore St #215<br>Oakland, CA 94619</p>
      <ul class="contact-list">
        <li><svg viewBox="0 0 24 24"><path d="M6.6 10.8a15 15 0 0 0 6.6 6.6l2.2-2.2c.3-.3.7-.4 1-.2 1.1.4 2.3.6 3.6.6.6 0 1 .4 1 1V20c0 .6-.4 1-1 1A17 17 0 0 1 3 4c0-.6.4-1 1-1h3.5c.6 0 1 .4 1 1 0 1.3.2 2.5.6 3.6.1.3 0 .7-.2 1z"/></svg>888-316-2790</li>
        <li><svg viewBox="0 0 24 24"><path d="M7 1h10a2 2 0 0 1 2 2v18a2 2 0 0 1-2 2H7a2 2 0 0 1-2-2V3a2 2 0 0 1 2-2zm0 3v14h10V4z"/></svg>510-742-3185</li>
        <li><svg viewBox="0 0 24 24"><path d="M4 4h16v16H4zm3 3v10h10V7z"/></svg>Lic.# 584261</li>
        <li><svg viewBox="0 0 24 24"><path d="M2 5h20v14H2zm2 2v.5l8 5 8-5V7l-8 5z"/></svg>walter@corvane-hvac.com</li>
      </ul>
    </div>
    <div class="web-band">corvane-hvac.com</div>
    <div class="band-end"></div>
  </section>
</main>
</body>
</html>
```